Professional Website

We are looking for a new website for our Staffing Company. Attached is a document with all the details and pages needed along with some examples of others websites.

We want a professional Look and feel around the same color theme as the attached Amber Compass.

We currently host our site on PageLoom.io. If the winning designer can also add to PageLoom, that is a plus.

```html
<!DOCTYPE html>
<html lang="en">
<head>
<meta charset="utf-8">
<title>HireBridge – Clerical &amp; Industrial Staffing</title>
<link rel="stylesheet" href="https://fonts.googleapis.com/css2?family=Montserrat:wght@400;500;600;700;800&display=swap">
<style>
:root{
  --brand:#2b2f96;
  --brand-dark:#232780;
  --ink:#1b1b1f;
  --text:#2c2c34;
  --topbar:#e4e3f2;
  --white:#ffffff;
}
*{box-sizing:border-box;margin:0;padding:0}
html,body{width:805px;height:1200px;overflow:hidden}
body{font-family:"Montserrat",sans-serif;color:var(--text);background:var(--white);position:relative}
.topbar{position:absolute;left:0;top:0;width:805px;height:27px;background:var(--topbar)}
.logins{position:absolute;right:0;top:0;height:27px;display:flex}
.logins a{display:flex;align-items:center;gap:5px;padding:0 17px;font-size:8.3px;font-weight:500;color:var(--ink);text-decoration:none;border-left:1px solid #b9b8d6;letter-spacing:.2px}
.logins svg{width:8px;height:9px;fill:var(--brand)}
.header{position:absolute;left:0;top:27px;width:805px;height:44px;background:var(--white)}
.brand{position:absolute;left:75px;top:-9px;display:flex;align-items:center;gap:6px}
.brand-mark{width:14px;height:14px;background:var(--brand);border-radius:50%}
.brand-name{font-size:26px;font-weight:800;color:var(--brand);letter-spacing:-.8px}
.nav{position:absolute;left:373px;top:17px;display:flex;gap:26px}
.nav a{font-size:9px;font-weight:500;color:var(--ink);text-decoration:none;position:relative}
.nav a.active{color:var(--brand)}
.nav a.active::after{content:"";position:absolute;left:1px;top:17px;width:28px;height:2px;background:var(--brand)}
.call{position:absolute;left:605px;top:6px;display:flex;align-items:center;gap:7px}
.call-icon{width:31px;height:31px;border-radius:50%;background:var(--brand);display:flex;align-items:center;justify-content:center}
.call small{display:block;font-size:9.5px;color:var(--text)}
.call strong{display:block;font-size:13.5px;font-weight:600;color:var(--ink)}
.hero{position:absolute;left:0;top:71px;width:805px;height:436px;background:linear-gradient(180deg,#dcdcdb 0%,#d3d2d0 60%,#8a6c52 68%,#b4977b 100%)}
.hero-photo{position:absolute;left:400px;top:80px;width:380px;height:340px;background:linear-gradient(135deg,#9a8a7e,#5e4c42 60%,#c7a07c);border-radius:6px;opacity:.55}
.hero h1{position:absolute;left:73px;top:97px;font-size:26px;font-weight:800;line-height:39px;color:var(--ink);letter-spacing:.1px}
.cta{position:absolute;left:75px;top:226px;display:flex;height:32px;background:var(--white)}
.cta a{display:flex;align-items:center;padding:0 0 0 8px;font-size:8.6px;font-weight:600;text-decoration:none}
.cta .seek{background:var(--brand);color:var(--white);width:130px}
.cta .hire{color:var(--brand);width:127px;padding-left:23px}
.cta-switch{position:absolute;left:124px;top:5px;width:22px;height:22px;border-radius:50%;background:var(--white);border:1px solid var(--brand);display:flex;align-items:center;justify-content:center}
.arrow-btn{position:absolute;top:198px;width:40px;height:40px;border-radius:50%;border:1px solid var(--brand);display:flex;align-items:center;justify-content:center}
.dots{position:absolute;left:385px;top:405px;display:flex;gap:5px;align-items:center}
.dots span{width:7px;height:7px;border-radius:50%;border:1px solid var(--white)}
.dots span.on{width:12px;height:12px;border-color:var(--brand);background:radial-gradient(var(--brand) 45%,transparent 50%)}
.team{position:absolute;left:0;top:699px;width:805px;height:247px;z-index:1;background:linear-gradient(180deg,#ffffff 0%,#f1f1f1 30%,#6b6e79 70%,#3d4150 100%)}
.why{position:absolute;left:0;top:560px;width:805px;text-align:center;z-index:2}
.why h2{font-size:25px;font-weight:800;color:var(--ink);letter-spacing:-.2px}
.why h2 span{color:var(--brand)}
.rule{display:block;margin:8px auto 0}
.why p{font-size:11.5px;line-height:20.5px;color:var(--text);margin:12px auto 0;width:600px}
.why p.lead{margin-top:16px}
.footer{position:absolute;left:0;top:946px;width:805px;height:254px;background:var(--brand);color:var(--white)}
.footer .brand{left:75px;top:70px}
.footer .brand-mark{background:var(--white)}
.footer .brand-name{color:var(--white)}
.col{position:absolute;top:46px}
.col h3{font-size:13.5px;font-weight:700;letter-spacing:.1px}
.col h3::after{content:"";display:block;width:34px;height:1.5px;background:var(--white);margin-top:9px}
.col ul{list-style:none;margin-top:10px}
.col li{font-size:9.2px;line-height:17.4px;font-weight:500}
.contact-item{display:flex;gap:8px;margin-top:8px;align-items:flex-start}
.contact-item svg{margin-top:6px;flex:none}
.contact-item small{display:block;font-size:7px;line-height:8px;opacity:.85}
.contact-item span{display:block;font-size:9.2px;line-height:13px;font-weight:500}
.legal{position:absolute;left:75px;top:197px;width:655px;border-top:1px solid rgba(255,255,255,.45)}
.legal p{position:absolute;left:0;top:17px;font-size:9.2px}
.legal nav{position:absolute;right:0;top:18px;font-size:8px;font-weight:500;display:flex;gap:15px}
.to-top{position:absolute;left:752px;top:181px;width:31px;height:31px;background:var(--white);border-radius:4px;display:flex;align-items:center;justify-content:center}
</style>
</head>
<body>
<div class="topbar">
  <nav class="logins">
    <a href="#"><svg viewBox="0 0 8 9"><circle cx="4" cy="2.2" r="2.2"/><path d="M0 9c0-3 1.6-4.5 4-4.5S8 6 8 9z"/></svg>EMPLOYEE LOGIN</a>
    <a href="#"><svg viewBox="0 0 8 9"><circle cx="4" cy="2.2" r="2.2"/><path d="M0 9c0-3 1.6-4.5 4-4.5S8 6 8 9z"/></svg>SWIFT PAY LOGIN</a>
    <a href="#"><svg viewBox="0 0 8 9"><circle cx="4" cy="2.2" r="2.2"/><path d="M0 9c0-3 1.6-4.5 4-4.5S8 6 8 9z"/></svg>LEDGER BANK LOGIN</a>
  </nav>
</div>
<header class="header">
  <div class="brand"><span class="brand-mark"></span><span class="brand-name">HireBridge</span></div>
  <nav class="nav">
    <a href="#" class="active">HOME</a><a href="#">JOBS</a><a href="#">ABOUT</a><a href="#">CONTACT</a>
  </nav>
  <div class="call">
    <div class="call-icon"><svg width="15" height="15" viewBox="0 0 24 24" fill="#fff"><path d="M6.6 10.8a15 15 0 0 0 6.6 6.6l2.2-2.2c.3-.3.7-.4 1-.2 1.1.4 2.3.6 3.6.6.6 0 1 .4 1 1V20c0 .6-.4 1-1 1A17 17 0 0 1 3 4c0-.6.4-1 1-1h3.5c.6 0 1 .4 1 1 0 1.3.2 2.5.6 3.6.1.3 0 .7-.2 1z"/></svg></div>
    <div><small>Call us now</small><strong>555-014-2290</strong></div>
  </div>
</header>

<section class="hero">
  <div class="hero-photo" role="img" aria-label="Photo of three professionals in a meeting at a wooden table"></div>
  <h1>RECRUITING AGENCY<br>FOR TEMPORARY AND<br>DIRECT HIRE EMPLOYEES</h1>
  <div class="cta">
    <a href="#" class="seek">I'M LOOKING FOR A JOB</a>
    <a href="#" class="hire">I NEED EMPLOYEES</a>
    <span class="cta-switch"><svg width="14" height="8" viewBox="0 0 14 8" fill="none" stroke="#2b2f96" stroke-width="1"><path d="M1 4h12M3.5 1.5 1 4l2.5 2.5M10.5 1.5 13 4l-2.5 2.5"/></svg></span>
  </div>
  <span class="arrow-btn" style="left:16px"><svg width="13" height="10" viewBox="0 0 13 10" fill="none" stroke="#2b2f96" stroke-width="1.3"><path d="M12 5H1M5 1 1 5l4 4"/></svg></span>
  <span class="arrow-btn" style="left:749px"><svg width="13" height="10" viewBox="0 0 13 10" fill="none" stroke="#2b2f96" stroke-width="1.3"><path d="M1 5h11M8 1l4 4-4 4"/></svg></span>
  <div class="dots"><span></span><span class="on"></span><span></span></div>
</section>

<div class="team" role="img" aria-label="Photo of six smiling job candidates seated against a white brick wall"></div>
<section class="why">
  <h2>WHY <span>HIREBRIDGE</span></h2>
  <svg class="rule" width="230" height="10" viewBox="0 0 230 10"><rect x="0" y="5" width="230" height="2" fill="#2b2f96"/><rect x="70" y="1" width="125" height="8" fill="#2b2f96"/><path d="M197 1l4 4-4 4M204 1l4 4-4 4M211 1l4 4-4 4M218 1l4 4-4 4" stroke="#2b2f96" stroke-width="2" fill="none"/></svg>
  <p class="lead">Greatest part of our daily job is that we are constantly bringing people together.</p>
  <p>Our Clients come to us in search of the perfect candidate and the job hunters approach us when they are in need of a job or looking for their next exciting role.</p>
  <p>Being able to work with and connect the two is incredibly satisfying. Not to mention that in today's current job market, employers are fighting for the top talent. This makes our employees and partners grateful for the help in finding it!</p>
</section>

<footer class="footer">
  <div class="brand"><span class="brand-mark"></span><span class="brand-name">HireBridge</span></div>
  <div class="col" style="left:296px"><h3>QUICK LINKS</h3><ul><li>Home</li><li>Jobs</li><li>About</li><li>Contact</li></ul></div>
  <div class="col" style="left:425px"><h3>AREAS WE SERVICE</h3><ul><li>Blue Island</li><li>Alsip</li><li>Romeoville</li></ul></div>
  <div class="col" style="left:599px"><h3>CONTACT US</h3>
    <div class="contact-item"><svg width="11" height="14" viewBox="0 0 11 14" fill="#fff"><path d="M5.5 0A5.5 5.5 0 0 0 0 5.5C0 9.5 5.5 14 5.5 14S11 9.5 11 5.5A5.5 5.5 0 0 0 5.5 0zm0 7.5a2 2 0 1 1 0-4 2 2 0 0 1 0 4z"/></svg><div><small>Address</small><span>88 Cedar Row, Milford<br>Texas, USA</span></div></div>
    <div class="contact-item"><svg width="11" height="11" viewBox="0 0 24 24" fill="#fff"><path d="M6.6 10.8a15 15 0 0 0 6.6 6.6l2.2-2.2c.3-.3.7-.4 1-.2 1.1.4 2.3.6 3.6.6.6 0 1 .4 1 1V20c0 .6-.4 1-1 1A17 17 0 0 1 3 4c0-.6.4-1 1-1h3.5c.6 0 1 .4 1 1 0 1.3.2 2.5.6 3.6.1.3 0 .7-.2 1z"/></svg><div><small>Phone</small><span>555-014-2290</span></div></div>
    <div class="contact-item"><svg width="12" height="9" viewBox="0 0 12 9" fill="none" stroke="#fff"><rect x=".5" y=".5" width="11" height="8"/><path d="M.5.5 6 5l5.5-4.5"/></svg><div><small>Mail</small><span>hello@hirebridge.co</span></div></div>
  </div>
  <div class="legal">
    <p>Copyright © 2022 | All Rights Reserved</p>
    <nav><span>TERMS &amp; CONDITIONS</span><span>|</span><span>PRIVACY POLICY</span></nav>
  </div>
  <span class="to-top"><svg width="8" height="5" viewBox="0 0 8 5" fill="none" stroke="#2b2f96" stroke-width="1.2"><path d="M1 4.5 4 1.5l3 3"/></svg></span>
</footer>
</body>
</html>
```